Veldmark Supplies Business Card

Professional business card that stand out to our potential customers. Front and back with clean modern design

Industry/Entity Type

Oil and gas

Contact Information for Business Card

Name, address, website , office phone and cell number

Requirements
Must have
• Editable files for each employee

```html
<!DOCTYPE html>
<html lang="en">
<head>
<meta charset="utf-8">
<title>Veldmark Supplies – Business Card</title>
<link rel="stylesheet" href="https://fonts.googleapis.com/css2?family=Montserrat:wght@500;600;800&display=swap">
<style>
  :root {
    --page-bg: #d9d9d9;
    --card-bg: #2a2a2b;
    --accent-red: #ec1c24;
    --accent-cyan: #00b3d6;
    --text-light: #f2f2f2;
    --pattern-cyan: #2f8fa5;
    --pattern-grey: #6d6a68;
    --pattern-red: #c6392c;
  }
  * { box-sizing: border-box; margin: 0; padding: 0; }
  html, body { width: 1200px; height: 900px; overflow: hidden; }
  body {
    background: var(--page-bg);
    font-family: "Montserrat", sans-serif;
    position: relative;
  }
  .card {
    position: absolute;
    left: 250px;
    width: 700px;
    height: 400px;
    border-radius: 22px;
    background: var(--card-bg);
    overflow: hidden;
    box-shadow: 0 10px 24px rgba(0,0,0,.25);
  }
  .card--back { top: 30px; }
  .card--front { top: 470px; }

  /* back side */
  .back-pattern {
    position: absolute;
    inset: 22px 26px;
    border-radius: 10px;
    background:
      linear-gradient(100deg, var(--pattern-cyan) 0%, var(--pattern-grey) 45%, var(--pattern-red) 100%);
    opacity: .55;
  }

  /* front side */
  .brand {
    position: absolute;
    left: 40px;
    top: 150px;
    width: 270px;
    display: flex;
    align-items: center;
    gap: 12px;
  }
  .brand__mark {
    width: 22px;
    height: 22px;
    background: var(--accent-red);
    flex: none;
  }
  .brand__name {
    font-weight: 800;
    font-size: 27px;
    letter-spacing: .5px;
    color: var(--accent-red);
    text-transform: uppercase;
    line-height: 1.1;
  }
  .divider {
    position: absolute;
    left: 330px;
    top: 70px;
    width: 2px;
    height: 260px;
    background: var(--accent-red);
  }
  .details {
    position: absolute;
    left: 360px;
    top: 62px;
    color: var(--text-light);
  }
  .details__name {
    font-weight: 800;
    font-size: 27px;
    color: var(--accent-red);
    text-transform: uppercase;
    letter-spacing: .5px;
  }
  .details__title {
    font-weight: 500;
    font-size: 17px;
    margin-top: 2px;
  }
  .details__address {
    font-weight: 500;
    font-size: 16px;
    line-height: 1.35;
    margin-top: 16px;
    padding-left: 24px;
  }
  .contact-list {
    list-style: none;
    margin-top: 16px;
  }
  .contact-list li {
    display: flex;
    align-items: center;
    gap: 12px;
    font-weight: 500;
    font-size: 15px;
    line-height: 1;
    margin-bottom: 9px;
  }
  .contact-icon {
    width: 20px;
    height: 20px;
    background: var(--accent-red);
    display: flex;
    align-items: center;
    justify-content: center;
    flex: none;
  }
  .contact-icon svg { width: 13px; height: 13px; }
</style>
</head>
<body>

<section class="card card--back" aria-label="Card back">
  <div class="back-pattern" role="img" aria-label="Repeating brand pattern fading from cyan to red"></div>
</section>

<section class="card card--front" aria-label="Card front">
  <div class="brand">
    <span class="brand__mark"></span>
    <span class="brand__name">Veldmark Supplies</span>
  </div>

  <div class="divider"></div>

  <div class="details">
    <p class="details__name">Dorian Kessel</p>
    <p class="details__title">President</p>
    <p class="details__address">4870 Harlow Ave, Ste<br>310, Ravenport, TX 79388</p>

    <ul class="contact-list">
      <li>
        <span class="contact-icon">
          <svg viewBox="0 0 16 16" fill="#fff"><path d="M3 2h3l1 3-2 1.2a8 8 0 0 0 4.8 4.8L11 9l3 1v3a1 1 0 0 1-1 1A12 12 0 0 1 2 3a1 1 0 0 1 1-1z"/></svg>
        </span>555-014-2731
      </li>
      <li>
        <span class="contact-icon">
          <svg viewBox="0 0 16 16" fill="none" stroke="#fff" stroke-width="1.6"><rect x="4.5" y="1.5" width="7" height="13" rx="1.2"/><line x1="7" y1="12" x2="9" y2="12"/></svg>
        </span>555-018-4406
      </li>
      <li>
        <span class="contact-icon">
          <svg viewBox="0 0 16 16" fill="none" stroke="#fff" stroke-width="1.5"><rect x="1.5" y="3.5" width="13" height="9"/><path d="M1.5 3.5 8 9l6.5-5.5"/></svg>
        </span>hello@veldmarksupply.net
      </li>
      <li>
        <span class="contact-icon">
          <svg viewBox="0 0 16 16" fill="none" stroke="#fff" stroke-width="1.4"><circle cx="8" cy="8" r="6"/><ellipse cx="8" cy="8" rx="2.6" ry="6"/><line x1="2" y1="8" x2="14" y2="8"/></svg>
        </span>www.veldmarksupply.net
      </li>
    </ul>
  </div>
</section>

</body>
</html>
```